Real estate agent website

I am a new real estate agent and in of a simple but powerful website that is linked to the local Multiple listing services (MLS). It should have a lending page that is connected to my customer relationship management (CRM) software. It must have an ability for potential customers to search for properties and be able to communicate with me easily.
Updates

Updates: The website themes must includes MLS-IDX integration with a grid layout and property slider so i can showcase featured properties. I also would like to have future where potential client can search and have alerts depending on a search criteria.

Industry/Entity Type

Real Estate

Coding

Coded - Design and coding required

Number of Pages Required

3 page

Requirements
Must have
• Home page, Resources page, About Me with contact me window page

```html
<!DOCTYPE html>
<html lang="en">
<head>
<meta charset="utf-8">
<title>Marisa Holloway Real Estate</title>
<link href="https://fonts.googleapis.com/css2?family=Montserrat:wght@500;600;700&family=Roboto:wght@400;500;700&display=swap" rel="stylesheet">
<style>
:root{
  --gold:#c9883a;
  --ink:#222222;
  --text:#333333;
  --line:#e3e3e3;
  --footer:#4a4c55;
  --white:#ffffff;
}
*{margin:0;padding:0;box-sizing:border-box}
html,body{width:1200px;height:2750px;overflow:hidden}
body{font-family:"Roboto",sans-serif;color:var(--text);background:var(--white);position:relative}
h1,h2,h3{font-family:"Montserrat",sans-serif}

/* brand name */
.brand{position:absolute;display:flex;align-items:center;gap:10px;white-space:nowrap;font-family:"Roboto",sans-serif;font-weight:500;font-size:22px;color:var(--white);letter-spacing:1px}
.brand-mark{width:14px;height:14px;background:var(--white);flex:none}

/* hero */
.hero{position:absolute;left:0;top:0;width:1200px;height:557px;overflow:hidden}
.hero-photo{position:absolute;inset:0;background:radial-gradient(ellipse at 62% 30%,#cfc6bd 0%,#a59a90 30%,#6f6a66 60%,#4a4848 100%)}
.hero-shade{position:absolute;inset:0;background:rgba(30,30,35,.35)}
.nav{position:absolute;top:40px;left:515px;display:flex;gap:34px}
.nav a{color:var(--white);font-size:15px;text-decoration:none}
.nav-search{position:absolute;left:1064px;top:41px}
.hero-title{position:absolute;top:210px;width:1200px;text-align:center;font-size:64px;font-weight:700;color:var(--white);white-space:nowrap}
.learn{position:absolute;top:312px;left:534px;width:132px;border-top:2px solid var(--white);padding-top:8px;color:var(--white);font-family:"Montserrat",sans-serif;font-weight:700;font-size:16px;white-space:nowrap}
.search{position:absolute;left:305px;top:384px;width:590px;height:64px;background:var(--white);border-radius:4px;display:flex;align-items:center}
.search .pin{margin-left:30px}
.search span{margin-left:20px;font-size:15px;color:#666}
.search-btn{position:absolute;right:0;top:0;width:75px;height:64px;background:var(--gold);border-radius:0 4px 4px 0;display:flex;align-items:center;justify-content:center}

/* about */
.about-photo{position:absolute;left:111px;top:649px;width:446px;height:367px;border-radius:40px 0 40px 0;background:linear-gradient(135deg,#e9e4df,#cfa88e 55%,#e8e2dc)}
.section-title{font-size:30px;font-weight:700;color:var(--ink)}
.rule{width:66px;height:2px;background:var(--gold)}
.about-copy{position:absolute;left:620px;top:643px;width:468px}
.about-copy .rule{margin-top:10px}
.about-copy p{margin-top:28px;font-size:15.5px;line-height:28.3px;text-align:justify;color:#444}
.btn{display:inline-block;background:var(--gold);color:var(--white);font-family:"Montserrat",sans-serif;font-weight:700;border-radius:22px;text-align:center}
.btn-more{position:absolute;left:620px;top:951px;width:151px;height:40px;line-height:40px;font-size:15px}

/* listings */
.listings{position:absolute;left:0;top:1109px;width:1200px;height:762px;overflow:hidden}
.listings-bg{position:absolute;inset:0;background:linear-gradient(90deg,#9b9a98 0%,#7c7770 35%,#4b4a4a 65%,#2e2f33 100%)}
.listings-shade{position:absolute;inset:0;background:rgba(20,20,20,.28)}
.listings-head{position:absolute;top:70px;width:1200px;text-align:center;color:var(--white)}
.listings-head .rule{margin:8px auto 0}
.card{position:absolute;top:172px;width:365px;height:454px;background:var(--white);overflow:hidden}
.card-img{height:244px;position:relative}
.tag{position:absolute;left:0;top:0;background:var(--gold);color:var(--white);font-size:11px;font-weight:700;padding:5px 12px 5px 11px;clip-path:polygon(0 0,100% 0,90% 100%,0 100%)}
.card-body{padding:0 24px}
.card-title{display:flex;justify-content:space-between;align-items:center;gap:10px;margin-top:12px;font-family:"Montserrat",sans-serif;font-weight:600;font-size:20px;color:var(--ink);white-space:nowrap}
.badge{width:62px;height:12px;background:#3b3b3b;border-radius:2px;flex:none}
.card-loc{display:flex;align-items:center;gap:10px;font-size:13px;margin-top:12px;color:#333;height:16px}
.card-feats{display:flex;align-items:center;border-top:1px solid var(--line);border-bottom:1px solid var(--line);margin-top:14px;height:62px;gap:18px;font-size:15px;color:#8a8a8a;white-space:nowrap}
.feat{display:flex;align-items:center;gap:10px}
.sqft{line-height:20px}
.card-foot{display:flex;justify-content:space-between;align-items:center;height:42px;font-size:13px;color:#333}
.price{color:var(--gold);font-size:17px;font-weight:500}
.arrows{position:absolute;top:662px;left:550px;display:flex;gap:22px}

/* contact */
.contact-head{position:absolute;top:1952px;width:1200px;text-align:center}
.contact-head .rule{margin:6px auto 0}
.info{position:absolute;left:106px;display:flex;gap:22px}
.info-icon{width:52px;height:52px;border-radius:50%;background:var(--white);box-shadow:0 2px 10px rgba(0,0,0,.12);display:flex;align-items:center;justify-content:center;flex:none}
.info h4{font-size:14px;font-weight:700;color:var(--ink);margin-top:4px}
.info p{font-size:15px;color:#555;line-height:22px;margin-top:6px}
.field{position:absolute;left:439px;width:322px;height:50px;border:1px solid #e2e2e2;box-shadow:0 1px 4px rgba(0,0,0,.05);display:flex;justify-content:space-between;align-items:center;padding:0 20px;font-size:14px;color:#666}
.message{position:absolute;left:788px;top:2048px;width:299px;height:168px;border:1px solid #e2e2e2;box-shadow:0 1px 4px rgba(0,0,0,.05);display:flex;justify-content:space-between;padding:18px 20px;font-size:14px;color:#666}
.btn-submit{position:absolute;left:788px;top:2237px;width:131px;height:41px;line-height:41px;font-size:13px}

/* footer */
.footer{position:absolute;left:0;top:2372px;width:1200px;height:378px;background:var(--footer);color:var(--white)}
.socials{position:absolute;left:111px;top:204px;display:flex;gap:9px}
.socials span{width:43px;height:43px;border-radius:50%;background:var(--white);display:block}
.f-col{position:absolute;top:90px}
.f-col h3{font-size:19px;font-weight:700}
.f-col .rule{width:36px;background:var(--white);margin-top:12px}
.f-col ul{list-style:none;margin-top:18px;font-size:16px;line-height:25.7px}
.f-contact li{display:flex;gap:16px;margin-bottom:12px;line-height:25px}
.f-contact svg{flex:none;margin-top:5px}
.copy{position:absolute;top:318px;width:1200px;text-align:center;font-size:15.5px}
</style>
</head>
<body>

<header class="hero">
  <div class="hero-photo" role="img" aria-label="Photo of a smiling agent using a phone at a laptop in a bright office"></div>
  <div class="hero-shade"></div>
  <div class="brand" style="left:113px;top:40px"><span class="brand-mark"></span>Marisa Holloway</div>
  <nav class="nav"><a href="#">Home</a><a href="#">About Us</a><a href="#">Featured Listings</a><a href="#">Lending</a><a href="#">Contact us</a></nav>
  <svg class="nav-search" width="22" height="22" viewBox="0 0 22 22"><circle cx="9" cy="9" r="6.5" fill="none" stroke="#fff" stroke-width="3"/><line x1="14" y1="14" x2="20" y2="20" stroke="#fff" stroke-width="3.4" stroke-linecap="round"/></svg>
  <h1 class="hero-title">Marisa Holloway Real Estate</h1>
  <div class="learn">LEARN MORE →</div>
  <div class="search">
    <svg class="pin" width="14" height="18" viewBox="0 0 14 18"><path d="M7 0a7 7 0 0 0-7 7c0 5 7 11 7 11s7-6 7-11a7 7 0 0 0-7-7z" fill="#bbb"/><circle cx="7" cy="7" r="2.5" fill="#fff"/></svg>
    <span>Start your search by city, Neighborhood or Zipcode</span>
    <div class="search-btn"><svg width="22" height="22" viewBox="0 0 22 22"><circle cx="9" cy="9" r="6.5" fill="none" stroke="#fff" stroke-width="3"/><line x1="14" y1="14" x2="20" y2="20" stroke="#fff" stroke-width="3.4" stroke-linecap="round"/></svg></div>
  </div>
</header>

<section class="about">
  <div class="about-photo" role="img" aria-label="Portrait photo of the agent"></div>
  <div class="about-copy">
    <h2 class="section-title">ABOUT ME</h2>
    <div class="rule"></div>
    <p>Lorem ipsum dolor sit amet, consectetur adipiscing elit, sed do eiusmod tempor incididunt ut labore et dolore magna aliqua. Ut enim ad minim veniam, quis nostrud exercitation ullamco laboris nisi ut aliquip ex ea commodo consequat. Duis aute irure dolor in reprehenderit in voluptate velit esse cillum dolore eu fugiat nulla pariatur. Excepteur sint occaecat cupidatat non proident, sunt in culpa qui officia deserunt mollit anim id est laborum.</p>
  </div>
  <a class="btn btn-more">More About</a>
</section>

<section class="listings">
  <div class="listings-bg" role="img" aria-label="Blurred photo of an agent in a suit handing over house keys"></div>
  <div class="listings-shade"></div>
  <div class="listings-head"><h2 class="section-title" style="color:#fff">FEATURED LISTINGS</h2><div class="rule"></div></div>

  <article class="card" style="left:-159px">
    <div class="card-img" role="img" aria-label="Photo of a beige townhouse with a garage in winter" style="background:linear-gradient(#b9ab94,#8e8577 70%,#e9ecef)"></div>
    <div class="card-body">
      <div class="card-title"><span style="margin-left:-40px">Maple Avenue</span><span class="badge"></span></div>
      <div class="card-loc"></div>
      <div class="card-feats"><span class="feat" style="margin-left:0">4 Baths</span><span class="feat sqft" style="margin-left:30px">2,361<br>Sqft</span></div>
      <div class="card-foot"><span></span><span class="price">$330,000</span></div>
    </div>
  </article>

  <article class="card" style="left:224px">
    <div class="card-img" role="img" aria-label="Photo of a two-storey grey house in snow" style="background:linear-gradient(#b9cfe6,#8b8c88 50%,#eef0f2 75%)"><span class="tag">FEATURED</span></div>
    <div class="card-body">
      <div class="card-title"><span>10482 Larkspur Way N</span><span class="badge"></span></div>
      <div class="card-loc"><svg width="10" height="13" viewBox="0 0 14 18"><path d="M7 0a7 7 0 0 0-7 7c0 5 7 11 7 11s7-6 7-11a7 7 0 0 0-7-7z" fill="#aaa"/></svg>Pine Hollow, MN 55091</div>
      <div class="card-feats">
        <span class="feat"><svg width="28" height="20" viewBox="0 0 28 20" fill="none" stroke="#bbb" stroke-width="1.5"><rect x="2" y="3" width="24" height="12"/><line x1="2" y1="15" x2="2" y2="19"/><line x1="26" y1="15" x2="26" y2="19"/></svg>3 Beds</span>
        <span class="feat"><svg width="26" height="20" viewBox="0 0 26 20" fill="none" stroke="#bbb" stroke-width="1.5"><path d="M2 10h22v4a4 4 0 0 1-4 4H6a4 4 0 0 1-4-4z"/><path d="M20 10V3h-4"/></svg>4 Baths</span>
        <span class="feat"><svg width="24" height="24" viewBox="0 0 24 24" fill="none" stroke="#bbb" stroke-width="1.5"><rect x="3" y="2" width="12" height="20"/><rect x="15" y="9" width="6" height="13"/></svg><span class="sqft">3,508<br>Sqft</span></span>
      </div>
      <div class="card-foot"><span>Listed 2 Day Ago</span><span class="price">$849,900</span></div>
    </div>
  </article>

  <article class="card" style="left:609px">
    <div class="card-img" role="img" aria-label="Photo of a split-level house with a truck in the driveway" style="background:linear-gradient(#6f98cf,#9a8f7b 45%,#7d7a74 80%)"><span class="tag">FEATURED</span></div>
    <div class="card-body">
      <div class="card-title"><span>27615 Alder Ridge Trail</span><span class="badge"></span></div>
      <div class="card-loc"><svg width="10" height="13" viewBox="0 0 14 18"><path d="M7 0a7 7 0 0 0-7 7c0 5 7 11 7 11s7-6 7-11a7 7 0 0 0-7-7z" fill="#aaa"/></svg>Brookfield, MN 55187</div>
      <div class="card-feats">
        <span class="feat"><svg width="28" height="20" viewBox="0 0 28 20" fill="none" stroke="#bbb" stroke-width="1.5"><rect x="2" y="3" width="24" height="12"/><line x1="2" y1="15" x2="2" y2="19"/><line x1="26" y1="15" x2="26" y2="19"/></svg>4 Beds</span>
        <span class="feat"><svg width="26" height="20" viewBox="0 0 26 20" fill="none" stroke="#bbb" stroke-width="1.5"><path d="M2 10h22v4a4 4 0 0 1-4 4H6a4 4 0 0 1-4-4z"/><path d="M20 10V3h-4"/></svg>2 Baths</span>
        <span class="feat"><svg width="24" height="24" viewBox="0 0 24 24" fill="none" stroke="#bbb" stroke-width="1.5"><rect x="3" y="2" width="12" height="20"/><rect x="15" y="9" width="6" height="13"/></svg><span class="sqft">1,890<br>Sqft</span></span>
      </div>
      <div class="card-foot"><span>Listed 2 Day Ago</span><span class="price">$365,000</span></div>
    </div>
  </article>

  <article class="card" style="left:991px">
    <div class="card-img" role="img" aria-label="Photo of a brick apartment building on a city street" style="background:linear-gradient(#4c7ec4,#7a5a45 50%,#9a8f87)"><span class="tag">FEATURED</span></div>
    <div class="card-body">
      <div class="card-title"><span>418 Willow Street 31</span></div>
      <div class="card-loc"><svg width="10" height="13" viewBox="0 0 14 18"><path d="M7 0a7 7 0 0 0-7 7c0 5 7 11 7 11s7-6 7-11a7 7 0 0 0-7-7z" fill="#aaa"/></svg>Riverton, MN 55236</div>
      <div class="card-feats">
        <span class="feat"><svg width="28" height="20" viewBox="0 0 28 20" fill="none" stroke="#bbb" stroke-width="1.5"><rect x="2" y="3" width="24" height="12"/><line x1="2" y1="15" x2="2" y2="19"/><line x1="26" y1="15" x2="26" y2="19"/></svg>2 Beds</span>
        <span class="feat"><svg width="26" height="20" viewBox="0 0 26 20" fill="none" stroke="#bbb" stroke-width="1.5"><path d="M2 10h22v4a4 4 0 0 1-4 4H6a4 4 0 0 1-4-4z"/><path d="M20 10V3h-4"/></svg>4 Baths</span>
      </div>
      <div class="card-foot"><span>Listed 1 Day Ago</span></div>
    </div>
  </article>

  <div class="arrows">
    <svg width="30" height="20" viewBox="0 0 30 20" fill="none" stroke="#fff" stroke-width="2"><line x1="2" y1="10" x2="28" y2="10"/><polyline points="10,2 2,10 10,18"/></svg>
    <svg width="42" height="20" viewBox="0 0 42 20" fill="none" stroke="#fff" stroke-width="2"><line x1="2" y1="10" x2="40" y2="10"/><polyline points="32,2 40,10 32,18"/></svg>
  </div>
</section>

<section class="contact">
  <div class="contact-head"><h2 class="section-title">CONTACT US</h2><div class="rule"></div></div>

  <div class="info" style="top:2064px">
    <div class="info-icon"><svg width="20" height="24" viewBox="0 0 14 18" fill="none" stroke="#d89a55" stroke-width="1.2"><path d="M7 1a6 6 0 0 0-6 6c0 4.5 6 10 6 10s6-5.5 6-10a6 6 0 0 0-6-6z"/><circle cx="7" cy="7" r="2.3"/></svg></div>
    <div><h4>LOCATION</h4><p>4120 Birchwood Ave Ste 310, Cedar<br>Point, Mn, 55480</p></div>
  </div>
  <div class="info" style="top:2163px">
    <div class="info-icon"><svg width="24" height="20" viewBox="0 0 24 20" fill="none" stroke="#d89a55" stroke-width="1.3"><rect x="2" y="4" width="20" height="14"/><polyline points="2,4 12,12 22,4"/></svg></div>
    <div><h4>EMAIL US</h4><p>mholloway.homes@example.com</p></div>
  </div>
  <div class="info" style="top:2237px">
    <div class="info-icon"><svg width="22" height="22" viewBox="0 0 24 24" fill="none" stroke="#d89a55" stroke-width="1.3"><path d="M5 3l4 1 1 5-2 2a12 12 0 0 0 5 5l2-2 5 1 1 4c-1 2-3 3-5 2A20 20 0 0 1 3 8c-1-2 0-4 2-5z"/></svg></div>
    <div><h4>CONTACT US</h4><p style="font-size:17px;font-weight:500">(555) 204-8816</p></div>
  </div>

  <div class="field" style="top:2048px">Your Name<svg width="14" height="14" viewBox="0 0 14 14"><circle cx="7" cy="7" r="6" fill="none" stroke="#555"/><circle cx="7" cy="5.5" r="2.2" fill="#555"/><path d="M3 11a4.5 4 0 0 1 8 0" fill="#555"/></svg></div>
  <div class="field" style="top:2108px">Email Address<svg width="14" height="12" viewBox="0 0 14 12" fill="none" stroke="#555" stroke-width="1.3"><rect x="1" y="1" width="12" height="10"/><polyline points="1,2 7,7 13,2"/></svg></div>
  <div class="field" style="top:2167px">Phone No<svg width="12" height="12" viewBox="0 0 24 24"><path d="M5 3l4 1 1 5-2 2a12 12 0 0 0 5 5l2-2 5 1 1 4c-1 2-3 3-5 2A20 20 0 0 1 3 8c-1-2 0-4 2-5z" fill="#555"/></svg></div>
  <div class="field" style="top:2227px">Address<svg width="9" height="12" viewBox="0 0 14 18"><path d="M7 0a7 7 0 0 0-7 7c0 5 7 11 7 11s7-6 7-11a7 7 0 0 0-7-7z" fill="#555"/><circle cx="7" cy="7" r="2.5" fill="#fff"/></svg></div>
  <div class="message">Message<svg width="15" height="13" viewBox="0 0 15 13" fill="none" stroke="#555" stroke-width="1.3"><ellipse cx="7.5" cy="6" rx="6.5" ry="4.5"/><path d="M4 10l-2 2.5 4-1.5"/></svg></div>
  <a class="btn btn-submit">SUBMIT</a>
</section>

<footer class="footer">
  <div class="brand" style="left:114px;top:126px"><span class="brand-mark"></span>Marisa Holloway</div>
  <div class="socials"><span aria-label="Social profile 1"></span><span aria-label="Social profile 2"></span><span aria-label="Social profile 3"></span><span aria-label="Social profile 4"></span></div>
  <div class="f-col" style="left:458px"><h3>Quick Links</h3><div class="rule"></div><ul><li>Home</li><li>About Us</li><li>Featured Listings</li><li>Lending</li><li>Contact us</li></ul></div>
  <div class="f-col" style="left:647px"><h3>Company</h3><div class="rule"></div><ul><li>Terms &amp; condtions</li><li>Privacy Policy</li><li>About Us</li><li>Support</li></ul></div>
  <div class="f-col f-contact" style="left:845px"><h3>Contact Us</h3><div class="rule"></div>
    <ul>
      <li><svg width="14" height="18" viewBox="0 0 14 18"><path d="M7 0a7 7 0 0 0-7 7c0 5 7 11 7 11s7-6 7-11a7 7 0 0 0-7-7z" fill="#fff"/><circle cx="7" cy="7" r="2.5" fill="#4a4c55"/></svg><span>4120 Birchwood Ave Ste 310, Cedar<br>Point, Mn, 55480</span></li>
      <li><svg width="17" height="17" viewBox="0 0 24 24"><path d="M5 3l4 1 1 5-2 2a12 12 0 0 0 5 5l2-2 5 1 1 4c-1 2-3 3-5 2A20 20 0 0 1 3 8c-1-2 0-4 2-5z" fill="#fff"/></svg><span>555-204-8816</span></li>
      <li><svg width="17" height="14" viewBox="0 0 17 14"><rect x="0" y="1" width="17" height="12" fill="#fff"/><polyline points="0,1 8.5,8 17,1" fill="none" stroke="#4a4c55" stroke-width="1.5"/></svg><span>mholloway.homes@example.com</span></li>
    </ul>
  </div>
  <div class="copy">©Copyrights 2023 Marisa Holloway &nbsp;| &nbsp;&nbsp;All Rights Reserved</div>
</footer>

</body>
</html>
```